Tri-Fold Brochure for Christian Author and Speaker

Lorna Whitfield is an inspirational author and speaker, sharing her testimony and encouraging others in their walk with Christ. A gifted writer, her work has been featured on Gently Radiant, Steadfast Mornings, and Hymns & Teacups Magazine (Fall 2011).

Lorna ‘s first book, Leaving the Lantern Room: Unmasking Hidden Snares in Ordinary Living, is an informative memoir and Bible study, recounting her journey from committed Christian to witch, medium, and ghost hunter for eight years until restored to faith in Jesus Christ. She was a contributing author to Walking Past the Shadows: A Candid View of Sorcery from Those Who Left by Dale Pennington and a consultant for the novel The Keeper of Marlow Hollow by Beacon Prize Winning Author, Helen Osgood.

Lorna’s second book, An Insider’s Guide to Spiritual Warfare: 20 Battle-Tested Strategies from Behind Enemy Lines, will be published by Harvest Lane Press for Fall 2014.

Lorna is a wife and mother. She enjoys writing, spending time with her family, taking long walks, listening to music of all kinds, and experiencing God’s daily gift called life.

You can read more about Lorna and see the look and feel we are going for at www.lornawhitfield.example

The brochure is to be used as a promotional tool to gain Lorna speaking engagements. You can see the topics she covers at http://www.lornawhitfield.example/speaking-engagements/.

More info can be found at: https://www.facebook.com/AuthorLornaWhitfield
https://www.facebook.com/VMUCX
https://www.facebook.com/LeavingtheLanternRoom
https://www.facebook.com/OpenDoorOutreach
http://www.opendooroutreach.example

I have uploaded 3 headshots, book covers for both of Lorna's books and the design layout in .EPS format from Swiftprintery.example where I will be getting printing done.

3 more days till the contest ends get your final designs in.

Reason: I'm extending this as I am tied up at a leadership conference and will not be able to give this the attention it deserves till the weekend.

Target Market(s)

Churches and women's groups. Lorna's current audience skews heavy to women on a 70/30 ratio.

Industry/Entity Type

Christian

Requirements
Must have
• Headshot I have uploaded 3
Quotes from previous speaking engagements you can find those at http://www.lornawhitfield.example/speaking-engagements/

```html
<!DOCTYPE html>
<html lang="en">
<head>
<meta charset="utf-8">
<title>Lorna Whitfield – Author &amp; Speaker</title>
<link rel="stylesheet" href="https://fonts.googleapis.com/css2?family=Jost:wght@400;800&family=Didact+Gothic&family=Marcellus+SC&family=Great+Vibes&display=swap">
<style>
  :root{
    --crimson:#b3124e;
    --maroon:#6c0a27;
    --blush:#f1cbd6;
    --panel:#fdf3f5;
    --ink:#5b4b4e;
    --white:#ffffff;
  }
  *{margin:0;padding:0;box-sizing:border-box}
  html,body{width:848px;height:1200px;overflow:hidden}
  body{background:var(--blush);font-family:"Didact Gothic",sans-serif;color:var(--ink);position:relative}
  .page{position:absolute;inset:0;overflow:hidden}
  .panel{position:absolute;left:18px;top:0;width:823px;height:1182px;background:var(--panel);border-radius:0 44px 0 44px}
  .lily-decoration{position:absolute;left:80px;top:120px;width:700px;height:820px;
    background:radial-gradient(ellipse at 50% 45%,rgba(247,214,222,.75) 0%,rgba(250,228,233,.45) 45%,rgba(253,243,245,0) 75%)}
  .base-band{position:absolute;left:0;bottom:0;width:848px;height:20px;background:var(--crimson)}

  .title-tab{position:absolute;left:492px;top:0;width:304px;height:164px;background:var(--crimson);
    border-radius:0 0 40px 40px;color:var(--white)}
  .title-tab .word{position:absolute;font-family:"Marcellus SC",serif;font-size:36px;letter-spacing:1px;line-height:1}
  .title-tab .author{left:24px;top:44px}
  .title-tab .speaker{left:80px;top:106px}
  .title-tab .amp{position:absolute;left:164px;top:56px;font-family:"Great Vibes",cursive;font-size:48px;line-height:1}

  .content{position:absolute;left:66px;top:80px;width:726px}
  .who{font-family:"Jost",sans-serif;color:var(--maroon);font-weight:800;font-size:21px;line-height:24px}
  .who .role{font-weight:400}
  .quote{font-size:16px;text-align:justify}
  .quote .name{color:var(--crimson)}

  .t-tea .who{width:400px}
  .t-tea .quote{margin-top:16px;line-height:32px}

  .t-pastor{margin-top:20px}
  .t-pastor::after{content:"";display:block;clear:both}
  .t-pastor .who{float:left;width:210px;text-align:center;margin:4px 14px 0 0;line-height:22px}
  .t-pastor .who .small{font-weight:400}
  .t-pastor .quote{line-height:32px}

  .lower-row{display:flex;justify-content:space-between;margin-top:34px}
  .t-youth{width:334px}
  .t-youth .who{padding-left:8px}
  .t-youth .quote{margin-top:12px;line-height:29px}
  .t-fitness{width:318px;margin-top:70px;margin-right:8px}
  .t-fitness .quote{margin-top:14px;line-height:30px}
</style>
</head>
<body>
<div class="page">
  <div class="panel"></div>
  <div class="lily-decoration" role="img" aria-label="Faint pale pink lily flower decoration behind the testimonials"></div>

  <div class="title-tab">
    <span class="word author">Author</span>
    <span class="amp">&amp;</span>
    <span class="word speaker">Speaker</span>
  </div>

  <main class="content">
    <section class="testimonial t-tea">
      <h2 class="who">Joan Mercer, Trinity Covenant<br>Church, Women’s Christmas<br>Tea <span class="role">Coordinator</span></h2>
      <p class="quote">“We had <span class="name">Lorna</span> speak at our Women’s Tea. Even though the weather was terrible in Northern Michigan we had a good turnout and I had several women tell me afterwards how blessed they were with <span class="name">Lorna’s</span> message. The emphasis was on putting Christ first during the holidays and read more.....</p>
    </section>

    <section class="testimonial t-pastor">
      <h2 class="who"><span class="small">Neil</span><br>Hartsfield,<br><span class="small">Pastor,</span><br>Calvary Reformed<br><span class="small">Church</span></h2>
      <p class="quote">“<span class="name">Lorna Whitfield</span> spoke at our church sharing with us her testimony which includes how she attempted to blend witchcraft with Christianity. Obviously, she discovered that there is no compromising of the Gospel and the Holy Spirit brought her back in an amazing way. Her story is gripping. It also serves as a warning to not blend religion “ala carte” and to pay close attention to the Word of God. Lorna notes well that we all have a spiritual hunger, and if we don’t satisfy it with Christ and His word, we may slip into any kind of spiritual offering. The church needs to hear her story. It is a wake up call to be aware of the continual influence of our culture pushing us into consideration of the paranormal and other strange spiritual activity. Read more......</p>
    </section>

    <div class="lower-row">
      <section class="testimonial t-youth">
        <h2 class="who">Doug Felton,<br>&nbsp;Youth Director,<br>CrossPoint<br><span class="role">Community Church</span></h2>
        <p class="quote">“I invited <span class="name">Lorna</span> to come to the youth group that I pastor to share her testimony. Her life went from accepting Jesus as her Lord and Savior, to allowing witchcraft to take a stronghold in her life. Eventually she repented of her deception, being redeemed by her Lord and Savior. It was a powerful night as <span class="name">Lorna</span> shared her story. She made the students very aware that witchcraft is not something to mess with. That witchcraft and other strongholds are of the devil and can destroy your life. read more......</p>
      </section>

      <section class="testimonial t-fitness">
        <h2 class="who">Marianne Tolliver,<br>&nbsp;&nbsp;&nbsp;Founder/Director,<br>FaithSteps<br>&nbsp;&nbsp;&nbsp;&nbsp;&nbsp;&nbsp;Fitness <span class="role">Ministry</span></h2>
        <p class="quote">“<span class="name">Lorna’s</span> unique background and remarkable experiences, passion for the gospel message, and communication skills provide a wealth of information which will fit into any ministry setting. She has a heart for people and seeing the captives set free–and a delightful way of communicating God’s message with joy!”</p>
      </section>
    </div>
  </main>

  <div class="base-band"></div>
</div>
</body>
</html>
```